Falkrin homes and renovations business card design.

Would like some new card designs utilizing my new logo that look professional. I am open to different colors on the logo or utilize the same ones we have. I like the original concept but would like to see some fresh ideas and build on what we have already done.

Target Market(s)

Custom home building industry, Real estate sales, Renovation projects.

Industry/Entity Type

Home Builder

Contact Information for Business Card

Falkrin Homes and Renovations
2871 96th Avenue
Corwell Ridge, Westland
T2R3W8
Home : 403- 718-4063 Cell: 403- 294-5170

My info is : Dax Falkrin, President and CEO
email: falkrinhomes@maildrop-example.net
Website: falkrinhomes-example.com
websit

Requirements
Must have
• Must Use my new logo design. I am open to different colors on the logo or utilize the same ones in the existing design. I can upload the original logo design if needed.

```html
<!DOCTYPE html>
<html lang="en">
<head>
<meta charset="utf-8">
<title>Falkrin Homes and Renovations – Business Card</title>
<link href="https://fonts.googleapis.com/css2?family=Roboto+Condensed:wght@400;700&display=swap" rel="stylesheet">
<style>
  :root {
    --backdrop: #d3d4d6;
    --purple: #4b3570;
    --purple-light: #7b58a6;
    --purple-faint: #6f56a0;
    --black: #000000;
    --white: #ffffff;
    --gold: #c8962a;
    --card-w: 760px;
    --card-h: 434px;
  }
  * { margin: 0; padding: 0; box-sizing: border-box; }
  html, body {
    width: 1200px; height: 1001px; overflow: hidden;
    background: var(--backdrop);
    font-family: "Roboto Condensed", "Arial Narrow", sans-serif;
  }
  .sheet {
    width: 1200px; height: 1001px;
    display: flex; flex-direction: column; align-items: center; justify-content: center;
    gap: 44px;
  }
  .card {
    position: relative;
    width: var(--card-w); height: var(--card-h);
    overflow: hidden;
    box-shadow: 0 4px 12px rgba(0,0,0,.25);
  }
  .card-art { position: absolute; inset: 0; width: 100%; height: 100%; }

  /* Front */
  .owner {
    position: absolute; top: 30px; right: 36px;
    text-align: right; color: var(--white);
  }
  .owner-name { font-weight: 700; font-size: 24px; }
  .owner-title { font-weight: 400; font-size: 24px; margin-top: 2px; }
  .brand {
    position: absolute; left: 48px; top: 120px;
    display: flex; align-items: center; gap: 12px;
  }
  .brand-mark { width: 18px; height: 18px; background: var(--gold); flex: none; }
  .brand-name {
    font-weight: 700; font-size: 26px; line-height: 1.15; color: var(--gold);
    text-transform: uppercase; letter-spacing: .5px;
  }
  .services {
    position: absolute; left: 40px; bottom: 34px;
    color: var(--white); font-weight: 700; font-size: 21px;
  }

  /* Back */
  .company {
    position: absolute; left: 300px; top: 60px;
    color: var(--white); font-weight: 700; font-size: 29px; line-height: 1.2;
    text-transform: uppercase;
  }
  .contact {
    position: absolute; left: 360px; bottom: 40px;
    color: var(--white); font-size: 20px; line-height: 1.35;
    list-style: none;
  }
  .brand-faint {
    position: absolute; left: 56px; bottom: 54px;
    display: flex; align-items: center; gap: 10px;
  }
  .brand-faint .brand-mark { width: 14px; height: 14px; background: var(--purple-faint); }
  .brand-faint .brand-name { font-size: 24px; color: var(--purple-faint); }
</style>
</head>
<body>
<main class="sheet">

  <section class="card card-front" aria-label="Card front">
    <svg class="card-art" viewBox="0 0 760 434" preserveAspectRatio="none" aria-hidden="true">
      <rect width="760" height="434" fill="var(--purple)"/>
      <path d="M0 300 C 240 280, 440 90, 610 72 C 685 64, 735 95, 760 125 L760 434 L0 434 Z" fill="var(--black)"/>
    </svg>
    <div class="owner">
      <p class="owner-name">Dax Falkrin</p>
      <p class="owner-title">President and CEO</p>
    </div>
    <div class="brand">
      <span class="brand-mark"></span>
      <span class="brand-name">Falkrin<br>Homes and Renovations</span>
    </div>
    <p class="services">Custom Home Building Industry, Real Estate Sales, Renovation Projects</p>
  </section>

  <section class="card card-back" aria-label="Card back">
    <svg class="card-art" viewBox="0 0 760 434" preserveAspectRatio="none" aria-hidden="true">
      <rect width="760" height="434" fill="var(--black)"/>
      <path d="M0 205 C 140 330, 290 330, 420 235 C 550 140, 650 100, 760 90 L760 434 L0 434 Z" fill="var(--purple-light)"/>
      <path d="M0 235 C 140 350, 290 350, 420 258 C 550 166, 650 128, 760 120 L760 434 L0 434 Z" fill="var(--purple)"/>
    </svg>
    <h1 class="company">Falkrin<br>Homes and Renovations</h1>
    <ul class="contact">
      <li>2871 96th Avenue Corwell Ridge, Westland, T2R3W8</li>
      <li>Email: falkrinhomes@maildrop-example.net</li>
      <li>Website: falkrinhomes-example.com</li>
      <li>Home : 403- 718-4063 Cell: 403- 294-5170</li>
    </ul>
    <div class="brand-faint">
      <span class="brand-mark"></span>
      <span class="brand-name">Falkrin</span>
    </div>
  </section>

</main>
</body>
</html>
```